The Q Collective Business Cards

We need a sleek looking business card for our real estate company. Looking for a clean, modern, eye catching design on a standard size business card.
Updates

No more submissions please! Thank you!

Target Market(s)

General Public/Real Estate Clients

Industry/Entity Type

Real Estate

Contact Information for Business Card

Cards will be customized for each agent.

Colors

Designer to choose only greyscale colors for use in the design.

Requirements
Must have
• Black, white, gray color pallet, Photo area for headshot on the front of the card

```html
<!DOCTYPE html>
<html lang="en">
<head>
<meta charset="UTF-8">
<title>The Q Collective – Business Card</title>
<link href="https://fonts.googleapis.com/css2?family=Montserrat:wght@500&family=Nunito:wght@700&family=Roboto:wght@400&display=swap" rel="stylesheet">
<style>
  :root {
    --page-bg: #2b2b2b;
    --card-back: #242424;
    --card-front: #1e1e1e;
    --ink: #f2f2f2;
    --ink-soft: #d8d8d8;
    --photo-top: #6a5a50;
    --photo-bottom: #cfcac6;
  }
  * { margin: 0; padding: 0; box-sizing: border-box; }
  html, body { width: 1200px; height: 1138px; overflow: hidden; background: var(--page-bg); }
  .stage { position: relative; width: 1200px; height: 1138px; }

  .card {
    position: absolute;
    width: 620px;
    height: 375px;
    border-radius: 16px;
    overflow: hidden;
  }

  .brand-name {
    display: flex; align-items: center; gap: 12px;
    font-family: "Montserrat", sans-serif;
    font-weight: 500;
    color: var(--ink);
    text-transform: uppercase;
    white-space: nowrap;
  }
  .brand-square { width: 12px; height: 12px; background: var(--ink); flex: none; }

  /* Back side */
  .card-back { left: 274px; top: 186px; background: var(--card-back); }
  .card-back .brand-name {
    position: absolute;
    left: 0; right: 0; top: 170px;
    justify-content: center;
    font-size: 26px;
    letter-spacing: 5px;
  }
  .brokerage {
    position: absolute;
    left: 28px; bottom: 26px;
    font-family: "Montserrat", sans-serif;
    font-weight: 500;
    font-size: 11px;
    letter-spacing: 0.4px;
    color: var(--ink);
    text-transform: uppercase;
  }

  /* Front side */
  .card-front { left: 276px; top: 608px; background: var(--card-front); }
  .headshot {
    position: absolute;
    left: 0; top: 36px;
    width: 312px; height: 339px;
    background: linear-gradient(180deg, var(--photo-top) 0%, #8c7a70 45%, var(--photo-bottom) 100%);
    border-bottom-left-radius: 16px;
  }
  .card-front .brand-name {
    position: absolute;
    right: 32px; top: 58px;
    justify-content: flex-end;
    font-size: 21px;
    letter-spacing: 3px;
    gap: 10px;
  }
  .card-front .brand-square { width: 10px; height: 10px; }
  .agent {
    position: absolute;
    right: 32px; top: 152px;
    text-align: right;
    color: var(--ink);
  }
  .agent-name { font-family: "Nunito", sans-serif; font-weight: 700; font-size: 25px; line-height: 30px; }
  .agent-title { font-family: "Roboto", sans-serif; font-size: 15.5px; line-height: 22px; color: var(--ink-soft); }
  .address {
    position: absolute;
    right: 32px; top: 226px;
    text-align: right;
    font-family: "Roboto", sans-serif;
    font-size: 15.5px;
    line-height: 24px;
    color: var(--ink-soft);
  }
  .contacts {
    position: absolute;
    right: 26px; top: 282px;
    list-style: none;
    font-family: "Roboto", sans-serif;
    font-size: 15.5px;
    color: var(--ink-soft);
  }
  .contacts li {
    display: flex; align-items: center; justify-content: flex-end; gap: 12px;
    height: 23.5px;
  }
  .contacts svg { width: 14px; height: 14px; fill: var(--ink-soft); flex: none; }
</style>
</head>
<body>
<main class="stage">

  <section class="card card-back" aria-label="Card back">
    <div class="brand-name"><span class="brand-square"></span>The Q Collective</div>
    <div class="brokerage">Harbor Point Realty</div>
  </section>

  <section class="card card-front" aria-label="Card front">
    <div class="headshot" role="img" aria-label="Agent headshot photo"></div>

    <div class="brand-name"><span class="brand-square"></span>The Q Collective</div>

    <div class="agent">
      <div class="agent-name">Maya Ellison Hart</div>
      <div class="agent-title">Real Estate Broker</div>
    </div>

    <div class="address">
      <div>4120 Magnolia Pkwy</div>
      <div>Riverton, LA, US 70123</div>
    </div>

    <ul class="contacts">
      <li>+1 555-014-2290
        <svg viewBox="0 0 16 16" aria-hidden="true"><path d="M1 5c0-2 3-3 7-3s7 1 7 3v1.5h-3.5V5h-7v1.5H1zM3 8h10l1.5 6h-13zM8 9.2a2 2 0 1 0 0 4 2 2 0 0 0 0-4z"/></svg>
      </li>
      <li>maya@riverhomesearch.com
        <svg viewBox="0 0 16 16" aria-hidden="true"><path d="M1 3h14v10H1zm1.5 1.5v.3L8 9l5.5-4.2v-.3zm0 2.2v4.8h11V6.7L8 10.9z"/></svg>
      </li>
      <li>www.riverhomesearch.com
        <svg viewBox="0 0 16 16" aria-hidden="true"><path d="M8 1a7 7 0 1 0 0 14A7 7 0 0 0 8 1zm-.7 1.6v2.6H5.2c.4-1.4 1.2-2.4 2.1-2.6zm1.4 0c.9.2 1.7 1.2 2.1 2.6H8.7zM4.9 3.2c-.3.6-.6 1.2-.8 2H2.9a5.6 5.6 0 0 1 2-2zm6.2 0a5.6 5.6 0 0 1 2 2h-1.2c-.2-.8-.5-1.4-.8-2zM2.5 6.5h1.4a11 11 0 0 0 0 3H2.5a5.6 5.6 0 0 1 0-3zm2.8 0h2v3h-2a9 9 0 0 1 0-3zm3.4 0h2a9 9 0 0 1 0 3h-2zm3.4 0h1.4a5.6 5.6 0 0 1 0 3h-1.4a11 11 0 0 0 0-3zM2.9 10.8h1.2c.2.8.5 1.4.8 2a5.6 5.6 0 0 1-2-2zm2.3 0h2.1v2.6c-.9-.2-1.7-1.2-2.1-2.6zm3.5 0h2.1c-.4 1.4-1.2 2.4-2.1 2.6zm3.2 0h1.2a5.6 5.6 0 0 1-2 2c.3-.6.6-1.2.8-2z"/></svg>
      </li>
    </ul>
  </section>

</main>
</body>
</html>
```